Site Redesign in WORDPRESS for a Aerial Survey Company

We are looking for an updated look to our website that reflects our aerial drone services. Our company is changing directions from helping to provide legal documentation for companies to operate UAVs for commercial operations, to now providing Aerial Data Collection services. We need the new website to focus on this new direction.

Wordpress Design (Uncoded - PSD layout only)

Current site: http://tornwickaviation.com/
Business card attached

VISUAL
********
The new pages should be visually top-notch, appealing, and more user-friendly to navigate, and represent our professionalism and level of expertise. We love the use of images, both great photography and technical. Our specialty is the use of Aerial LiDAR.

Our current site uses the Mallow template.

Colors: I've attached the Pantone for our logo colors

Fonts: Simple, clean and professional. We are not worried about specific fonts so long as they tie or compliment our logo.

STRUCTURE
****************
In the attached document I have laid out the pages we would like to have and the content outline of the content these pages will include.

We're happy to answer you questions in the comments and to provide quick feedback and additional info if necessary.

Target Market(s)

Agricultural and Engineering firms

Industry/Entity Type

Agribusiness

Coding

Coded - Design and coding required

Number of Pages Required

5+ page

Font styles to use
Sans Serif

Colors
0392cd
9bcb3c
ffffff

Requirements
Must have
• We need at a minimum a design with the Home/Landing, Services, and about. Need to be able to adapt the site as we add new services and increase our partnerships.
• Please provide in WordPress format.
• Links to social media: Facebook, Twitter, Instagram
Nice to have
• We like parrallax, but in the end it's about the overall feel of the site.
Should not have
• Please, professional designs only.

```html
<!DOCTYPE html>
<html lang="en">
<head>
<meta charset="utf-8">
<title>Tornwick Aviation — Aerial Survey Drone Company</title>
<link href="https://fonts.googleapis.com/css2?family=Open+Sans:wght@300;400;600;700&display=swap" rel="stylesheet">
<style>
:root{
  --blue:#2a85d2;
  --blue-dark:#1f6fb5;
  --green:#8dc63f;
  --ink:#333a40;
  --muted:#8a8f94;
  --white:#ffffff;
  --dark:#3c4144;
  --panel:#5b5e60;
  --light:#f3f5f6;
}
*{margin:0;padding:0;box-sizing:border-box}
html,body{width:1200px;height:3734px;overflow:hidden}
body{position:relative;font-family:"Open Sans",Arial,sans-serif;color:var(--ink);background:var(--white)}

/* header */
.site-header{position:absolute;left:0;top:0;width:1200px;height:95px;background:var(--white)}
.brand{position:absolute;left:100px;top:20px;display:flex;align-items:center;gap:10px}
.brand-mark{width:40px;height:40px;background:var(--blue)}
.brand-name{font-weight:700;font-size:19px;line-height:21px;color:var(--blue);letter-spacing:1px}
.main-nav{position:absolute;top:40px;left:0;width:1200px;font-size:12.5px;color:#555}
.main-nav a{position:absolute;text-decoration:none;color:#555}
.main-nav a.current{color:var(--blue)}

/* hero */
.hero{position:absolute;left:0;top:95px;width:1200px;height:552px;
  background:linear-gradient(180deg,#b9c3c8 0%,#9aa69a 30%,#5d7a45 55%,#3f5f33 80%,#6b8fa8 100%)}
.hero-drone{position:absolute;left:160px;top:260px;width:460px;height:300px;
  background:radial-gradient(ellipse at center,rgba(245,245,240,.85) 0%,rgba(230,230,210,.6) 45%,rgba(255,255,255,0) 72%)}
.hero-title{position:absolute;right:97px;top:152px;text-align:right;color:var(--white);
  font-weight:300;font-size:44px;line-height:58px;letter-spacing:.5px}
.hero-title strong{font-weight:700}
.hero-arrow{position:absolute;top:300px;width:30px;height:36px;background:rgba(255,255,255,.35);border-radius:4px}

/* shared section heading */
.section-title{position:absolute;left:0;width:1200px;text-align:center;font-weight:700;font-size:23px;letter-spacing:.5px;color:var(--blue)}
.section-title .accent{color:var(--green)}
.section-rule{position:absolute;left:588px;width:24px;height:24px;background:#b7bcc0}

/* services */
.services{position:absolute;left:0;top:647px;width:1200px;height:511px;
  background:linear-gradient(180deg,#f7f8f9 0%,#eef1f2 45%,#f4f6f7 100%)}
.services-intro{position:absolute;left:0;top:103px;width:1200px;text-align:center;font-size:14px;line-height:25px;color:#6d7378}
.service{position:absolute;display:flex;align-items:center;gap:14px;font-weight:700;font-size:12.5px;color:var(--ink);text-transform:uppercase}
.service-icon{width:64px;height:64px;border-radius:50%;background:var(--blue);display:flex;align-items:center;justify-content:center;flex:none}

/* capabilities */
.capabilities{position:absolute;left:0;top:1158px;width:1200px;height:642px;
  background:linear-gradient(180deg,#4a4f52 0%,#3a3e40 50%,#2f3335 100%)}
.cap-card{position:absolute;top:114px;width:478px;height:471px}
.cap-photo{height:224px}
.cap-band{height:72px;background:var(--blue);color:var(--white);font-size:23px;font-weight:600;letter-spacing:1px;text-align:center;line-height:72px}
.cap-text{height:175px;background:var(--panel);color:#eceeef;font-size:11.5px;line-height:24px;text-align:center;padding:22px 40px 0}

/* about */
.about{position:absolute;left:0;top:1800px;width:1200px;height:565px;
  background:linear-gradient(180deg,#e6eef4 0%,#c9d7e1 50%,#dfe7ec 100%)}
.member{position:absolute;top:217px;width:241px;height:254px;background:var(--blue);text-align:center;color:var(--white)}
.member-photo{position:absolute;left:53px;top:-100px;width:134px;height:134px;border-radius:50%;border:5px solid var(--green);background:linear-gradient(180deg,#f2f2f2,#c9cdd0)}
.member-name{position:absolute;left:0;top:60px;width:100%;font-weight:600;font-size:16px;letter-spacing:.5px}
.member-role{position:absolute;left:18px;top:92px;width:205px;font-size:11px;line-height:19px;color:#e2eefa}
.more-btn{position:absolute;left:66px;top:186px;width:108px;height:40px;border:1px solid rgba(255,255,255,.75);font-size:12px;line-height:38px;color:var(--white)}

/* partners */
.partners{position:absolute;left:0;top:2365px;width:1200px;height:192px;background:var(--white)}
.partner{position:absolute;top:110px;height:34px;background:#d9dcdf}
.partner-arrow{position:absolute;top:112px;font-size:22px;color:#b5b9bd}

/* blog */
.blog{position:absolute;left:0;top:2557px;width:1200px;height:625px;
  background:linear-gradient(180deg,#eef0ef 0%,#e2e6e3 50%,#eceeed 100%)}
.post{position:absolute;top:130px;width:316px;height:450px;background:var(--white);box-shadow:0 2px 6px rgba(0,0,0,.12)}
.post-photo{height:201px}
.post-title{position:absolute;left:13px;top:214px;font-size:19px;font-weight:600;color:var(--blue)}
.post-meta{position:absolute;left:13px;top:247px;font-size:9px;color:#9aa0a5;text-transform:uppercase;letter-spacing:.3px}
.post-text{position:absolute;left:13px;top:268px;width:292px;font-size:10.5px;line-height:17px;color:#9aa0a5}
.read-btn{position:absolute;left:13px;top:396px;width:102px;height:36px;background:var(--blue);color:var(--white);font-size:12px;font-weight:600;line-height:36px;text-align:center;border-radius:3px}

/* contact */
.contact{position:absolute;left:0;top:3182px;width:1200px;height:478px;
  background:linear-gradient(180deg,#4d5458 0%,#5a5e5c 40%,#7a6e62 75%,#6e6a66 100%)}
.contact .section-title{color:var(--white)}
.field{position:absolute;left:361px;width:478px;background:var(--white);font-size:11px;color:#a5aaae;padding:0 0 0 14px;display:flex;align-items:center;gap:8px}
.field.message{align-items:flex-start;padding-top:10px}
.submit{position:absolute;left:364px;top:375px;width:154px;height:48px;background:var(--green);color:var(--white);font-weight:700;font-size:13px;letter-spacing:1px;text-align:center;line-height:48px}

/* footer */
.site-footer{position:absolute;left:0;top:3660px;width:1200px;height:74px;background:var(--blue);color:var(--white);font-size:12px}
.footer-copy{position:absolute;left:100px;top:29px}
.footer-social{position:absolute;left:845px;top:22px;display:flex;align-items:center;gap:12px}
.social-dot{width:32px;height:32px;border-radius:50%;border:1.5px solid rgba(255,255,255,.85)}
</style>
</head>
<body>

<header class="site-header">
  <div class="brand"><span class="brand-mark"></span><span class="brand-name">TORNWICK<br>AVIATION</span></div>
  <nav class="main-nav">
    <a class="current" style="left:476px">Home</a>
    <a style="left:560px">Services</a>
    <a style="left:657px">Capabilities</a>
    <a style="left:776px">About Us</a>
    <a style="left:880px">Partners</a>
    <a style="left:981px">Blog</a>
    <a style="left:1056px">Contact</a>
  </nav>
</header>

<section class="hero" role="img" aria-label="Quadcopter drone flying over a green forested valley with mountains and a lake">
  <div class="hero-drone"></div>
  <h1 class="hero-title">WE ARE AN AERIAL SURVEY<br><strong>DRONE</strong> COMPANY</h1>
  <span class="hero-arrow" style="left:26px"></span>
  <span class="hero-arrow" style="right:26px"></span>
</section>

<section class="services">
  <h2 class="section-title" style="top:26px">TORNWICK <span class="accent">SERVICES</span></h2>
  <span class="section-rule" style="top:68px"></span>
  <p class="services-intro">Our company continues to push the envelope in creating unique solutions and processes for all services and resources we deliver,<br>as we strive to create long-term business partnerships.</p>

  <div class="service" style="left:100px;top:170px"><span class="service-icon"><svg width="28" height="28" viewBox="0 0 24 24" fill="#fff"><path d="M5 20c0-9 6-15 15-15-1 9-6 14-15 15z"/></svg></span>Precision Agriculture</div>
  <div class="service" style="left:435px;top:170px"><span class="service-icon"><svg width="26" height="28" viewBox="0 0 24 24" fill="#fff"><path d="M12 2c4 6 7 9 7 13a7 7 0 0 1-14 0c0-4 3-7 7-13z"/></svg></span>Exploration, Oil, Gas, &amp; Mineral</div>
  <div class="service" style="left:851px;top:170px"><span class="service-icon"><svg width="28" height="28" viewBox="0 0 24 24" fill="#fff"><path d="M12 2l5 7h-3l5 6h-4l4 5H5l4-5H5l5-6H7z"/><rect x="11" y="20" width="2" height="3"/></svg></span>FLLIR/IR</div>

  <div class="service" style="left:100px;top:282px"><span class="service-icon"><svg width="26" height="28" viewBox="0 0 24 24" fill="#fff"><path d="M12 2c1 4 6 6 6 12a6 6 0 0 1-12 0c0-3 2-5 3-6 0 2 1 3 2 3 0-4-1-6 1-9z"/></svg></span>Public Services</div>
  <div class="service" style="left:435px;top:282px"><span class="service-icon"><svg width="28" height="28" viewBox="0 0 24 24" fill="none" stroke="#fff" stroke-width="2.6"><circle cx="10" cy="10" r="6"/><path d="M15 15l6 6"/></svg></span>Commercial &amp; Industrial Inspections</div>
  <div class="service" style="left:851px;top:282px"><span class="service-icon"><svg width="28" height="28" viewBox="0 0 24 24" fill="#fff"><path d="M12 3l9 4-9 4-9-4z"/><path d="M3 11l9 4 9-4v2l-9 4-9-4z"/><path d="M3 16l9 4 9-4v2l-9 4-9-4z"/></svg></span>GIS &amp; Mapping</div>

  <div class="service" style="left:100px;top:394px"><span class="service-icon"><svg width="28" height="28" viewBox="0 0 24 24" fill="#fff"><rect x="2" y="7" width="14" height="11" rx="2"/><path d="M16 11l6-4v11l-6-4z"/></svg></span>Video &amp; Still Images</div>
  <div class="service" style="left:435px;top:394px"><span class="service-icon"><svg width="28" height="28" viewBox="0 0 24 24" fill="#fff"><path d="M12 21l-8-8a5 5 0 0 1 8-6 5 5 0 0 1 8 6z"/></svg></span>UAV Flight Training &amp; Consulting</div>
  <div class="service" style="left:851px;top:394px"><span class="service-icon"><svg width="28" height="28" viewBox="0 0 24 24" fill="#fff"><path d="M2 20l7-11 4 5 3-4 6 10z"/><circle cx="17" cy="6" r="2"/></svg></span>Section 333 Exemptions</div>
</section>

<section class="capabilities" role="img" aria-label="Dark mountain landscape behind the capabilities panels">
  <h2 class="section-title" style="top:26px">TORNWICK <span class="accent">CAPABILITIES</span></h2>
  <article class="cap-card" style="left:100px">
    <div class="cap-photo" role="img" aria-label="Yellow quadcopter drone hovering above snowy mountains under a blue sky" style="background:linear-gradient(180deg,#5f9ed8 0%,#a9cdea 55%,#e8eef2 80%,#8aa1b3 100%)"></div>
    <div class="cap-band">DRONES</div>
    <p class="cap-text">Our deep experience in regulations and operations allows us to solve complex and challenging exceptions.A comprehensive package for those just starting out. Includes all documents needed to operate efficiently and professionally.</p>
  </article>
  <article class="cap-card" style="left:625px">
    <div class="cap-photo" role="img" aria-label="Gimbal-mounted aerial camera sensor against a cloudy sky" style="background:linear-gradient(160deg,#dfe5ea 0%,#b8c2ca 40%,#6d7880 70%,#aebccb 100%)"></div>
    <div class="cap-band">CAMERAS</div>
    <p class="cap-text">Our deep experience in regulations and operations allows us to solve complex and challenging exceptions.A comprehensive package for those just starting out. Includes all documents needed to operate efficiently and professionally.</p>
  </article>
</section>

<section class="about">
  <h2 class="section-title" style="top:46px">ABOUT US</h2>
  <span class="section-rule" style="top:88px"></span>
  <article class="member" style="left:100px">
    <div class="member-photo" role="img" aria-label="Portrait of Marla Denholt"></div>
    <h3 class="member-name">MARLA DENHOLT</h3>
    <p class="member-role">(CEO; Operations &amp; Regulatory Specialist and an Airline Transport Pilot)</p>
    <span class="more-btn">MORE INFO »</span>
  </article>
  <article class="member" style="left:356px">
    <div class="member-photo" role="img" aria-label="Portrait of Owen Castell"></div>
    <h3 class="member-name">OWEN CASTELL</h3>
    <p class="member-role">(President; Operations &amp; Regulatory Specialist and an Airline Transport Pilot)</p>
    <span class="more-btn">MORE INFO »</span>
  </article>
  <article class="member" style="left:612px">
    <div class="member-photo" role="img" aria-label="Portrait of Rhys"></div>
    <h3 class="member-name">RHYS</h3>
    <p class="member-role">(Director; Operations; Specializes in Supply Chain and Network Optimization)</p>
    <span class="more-btn">MORE INFO »</span>
  </article>
  <article class="member" style="left:869px">
    <div class="member-photo" role="img" aria-label="Portrait of Victor Ashby"></div>
    <h3 class="member-name">VICTOR ASHBY</h3>
    <p class="member-role">(Partner; NAA Deputy Director of Flight Standards, Retired and Helicopter Pilot)</p>
    <span class="more-btn">MORE INFO »</span>
  </article>
</section>

<section class="partners">
  <h2 class="section-title" style="top:30px">OUR PARTNERS</h2>
  <span class="section-rule" style="top:70px"></span>
  <span class="partner-arrow" style="left:95px">‹</span>
  <span class="partner" style="left:150px;width:110px;background:#e8a060"></span>
  <span class="partner" style="left:325px;width:185px"></span>
  <span class="partner" style="left:580px;width:105px;background:#e6ded0"></span>
  <span class="partner" style="left:790px;width:95px;background:#cfe3cf"></span>
  <span class="partner" style="left:965px;width:90px;background:#d6e2ef"></span>
  <span class="partner-arrow" style="left:1090px">›</span>
</section>

<section class="blog">
  <h2 class="section-title" style="top:36px">BLOG <span class="accent">&amp; UPCOMING EVENTS</span></h2>
  <span class="section-rule" style="top:78px"></span>
  <article class="post" style="left:100px">
    <div class="post-photo" role="img" aria-label="Pilot trainee wearing an aviation headset beside an instructor" style="background:linear-gradient(180deg,#e9ecec 0%,#c9cfd2 50%,#9aa5a0 100%)"></div>
    <h3 class="post-title">Flight Training</h3>
    <p class="post-meta">October 26, 2015 &nbsp;&nbsp; 10 Comments</p>
    <p class="post-text">Nam libero tempore, cum soluta nobis est eligendi optio cumque nihil impedit quo minus id quod maxime placeat facere possimus, omnis voluptas assumenda est, omnis dolor repellendus.</p>
    <span class="read-btn">Read More »</span>
  </article>
  <article class="post" style="left:443px">
    <div class="post-photo" role="img" aria-label="Business travellers walking beside a private jet" style="background:linear-gradient(180deg,#cfdbe6 0%,#b9c5cf 50%,#6f7478 100%)"></div>
    <h3 class="post-title">Aviation Consulting</h3>
    <p class="post-meta">October 26, 2015 &nbsp;&nbsp; 8 Comments</p>
    <p class="post-text">Nam libero tempore, cum soluta nobis est eligendi optio cumque nihil impedit quo minus id quod maxime placeat facere possimus, omnis voluptas assumenda est, omnis dolor repellendus.</p>
    <span class="read-btn">Read More »</span>
  </article>
  <article class="post" style="left:787px">
    <div class="post-photo" role="img" aria-label="Business jet parked on a runway under a blue sky" style="background:linear-gradient(180deg,#4f8fcf 0%,#a8c8e6 55%,#9ba2a6 80%,#6f7a70 100%)"></div>
    <h3 class="post-title">Standard Package</h3>
    <p class="post-meta">October 26, 2015 &nbsp;&nbsp; 12 Comments</p>
    <p class="post-text">Nam libero tempore, cum soluta nobis est eligendi optio cumque nihil impedit quo minus id quod maxime placeat facere possimus, omnis voluptas assumenda est, omnis dolor repellendus.</p>
    <span class="read-btn">Read More »</span>
  </article>
</section>

<section class="contact" role="img" aria-label="Aerial view of a town at dusk behind the contact form">
  <h2 class="section-title" style="top:34px">CONTACT <span class="accent">US</span></h2>
  <span class="section-rule" style="top:76px"></span>
  <div class="field" style="top:135px;height:34px"><svg width="11" height="11" viewBox="0 0 24 24" fill="#b0b5b9"><circle cx="12" cy="7" r="5"/><path d="M2 23c1-6 5-9 10-9s9 3 10 9z"/></svg>Your Name</div>
  <div class="field" style="top:184px;height:34px"><svg width="12" height="10" viewBox="0 0 24 18" fill="none" stroke="#b0b5b9" stroke-width="2.4"><rect x="1" y="1" width="22" height="16"/><path d="M1 1l11 9 11-9"/></svg>Your Email</div>
  <div class="field message" style="top:228px;height:112px"><svg width="11" height="11" viewBox="0 0 24 24" fill="#b0b5b9"><path d="M3 17l12-12 4 4-12 12H3z"/></svg>Your Message</div>
  <span class="submit">SUBMIT</span>
</section>

<footer class="site-footer">
  <p class="footer-copy">TORNWICK AVIATION. © 2016 | Privacy Policy</p>
  <div class="footer-social">
    <span>Connected Us On:</span>
    <span class="social-dot" aria-label="Social link one"></span>
    <span class="social-dot" aria-label="Social link two"></span>
    <span class="social-dot" aria-label="Social link three"></span>
  </div>
</footer>

</body>
</html>
```